Business Card for Multi-Brand Sportswear Company

We are looking for a business card which represents our company and the multiple brands within it.

The company: Fen Athletics (LTD)
The brands: Fen, TavaPuni, ElmStretch, Grit and Rain

Employees using these cards would be representing Fen Athletics, rather than any of the individual brands. You will see a current design within the uploaded files, to give some inspiration. The actual text of the brands is not necessary, but the logos should be on there is some format.

Our creative minds on this are stretched, so we are looking for someone to make this their own, and show us what a good business card should look like.

We may like to get these printed with spot gloss, so keep that in mind with your designs.

www.fenathletics.co.uk

Industry/Entity Type

Business

Contact Information for Business Card

Leo Pemberton-Hale
Operations Manager
(+44) 1632 960 418
Leo@fenathletics.co.uk
www.fenathletics.co.uk

Font styles to use
Sans Serif
Other font styles liked:
• Eurostile

Colors
ffffff

Requirements
Nice to have
• Dark (black) background

```html
<!DOCTYPE html>
<html lang="en">
<head>
<meta charset="utf-8">
<title>Fen Athletics – Business Card</title>
<link href="https://fonts.googleapis.com/css2?family=Quicksand:wght@500;600&display=swap" rel="stylesheet">
<style>
  :root {
    --backdrop: #8c8c8c;
    --card: #2b2a29;
    --gloss: #77736f;
    --white: #ffffff;
    --soft-white: #e9e9e9;
    --plum: #5f4b63;
    --plum-text: #b9a3bd;
    --red: #d42a2a;
    --grey-mark: #8f8f8f;
  }
  * { margin: 0; padding: 0; box-sizing: border-box; }
  html, body { width: 1200px; height: 854px; overflow: hidden; }
  body {
    background: var(--backdrop);
    font-family: "Quicksand", sans-serif;
    position: relative;
  }
  .card {
    position: absolute;
    top: 281px;
    width: 512px;
    height: 293px;
    background: var(--card);
    color: var(--white);
  }
  .card--front { left: 69px; }
  .card--back { left: 600px; }

  .wordmark {
    position: absolute;
    color: var(--gloss);
    font-weight: 600;
    white-space: nowrap;
    line-height: 1;
    letter-spacing: -0.3px;
  }
  .card--front .wordmark { left: 24px; top: 103px; font-size: 35px; }
  .card--back .wordmark { left: 50px; top: 104px; font-size: 66px; }

  .brand-row {
    position: absolute;
    display: flex;
    align-items: center;
    white-space: nowrap;
    font-weight: 600;
  }
  .card--front .brand-row { left: 24px; top: 182px; gap: 13px; font-size: 9px; }
  .card--back .brand-row { left: 62px; top: 234px; gap: 26px; font-size: 16px; }
  .brand { display: flex; align-items: center; gap: 4px; }
  .card--back .brand { gap: 7px; }
  .brand__dot { display: inline-block; width: 8px; height: 8px; }
  .card--back .brand__dot { width: 14px; height: 14px; }
  .brand--elm { color: var(--plum-text); }
  .brand--elm .brand__dot { background: var(--plum); }
  .brand--grit { color: var(--red); }
  .brand--fen { color: var(--white); }
  .brand--tava { color: var(--grey-mark); }
  .brand--tava .brand__dot { border: 1.5px solid var(--grey-mark); border-radius: 50%; }

  .person {
    position: absolute;
    right: 28px;
    top: 114px;
    text-align: right;
  }
  .person__name { font-size: 19px; font-weight: 600; letter-spacing: -0.2px; }
  .person__role { font-size: 15px; font-weight: 500; margin-top: 9px; color: var(--soft-white); }

  .contact {
    position: absolute;
    left: 313px;
    top: 196px;
    list-style: none;
    font-size: 14px;
    font-weight: 500;
    color: var(--soft-white);
  }
  .contact li { display: flex; align-items: center; gap: 9px; height: 24px; }
  .contact svg { width: 12px; height: 12px; flex: none; }
</style>
</head>
<body>
  <section class="card card--front">
    <div class="wordmark">Fen Athletics</div>

    <div class="brand-row">
      <span class="brand brand--elm"><i class="brand__dot"></i>ElmStretch</span>
      <span class="brand brand--grit">Grit and Rain</span>
      <span class="brand brand--fen">Fen</span>
      <span class="brand brand--tava"><i class="brand__dot"></i>TavaPuni</span>
    </div>

    <div class="person">
      <div class="person__name">Leo Pemberton-Hale</div>
      <div class="person__role">Operations Manager</div>
    </div>

    <ul class="contact">
      <li>
        <svg viewBox="0 0 12 12" fill="none" stroke="#e9e9e9" stroke-width="1.2" stroke-linejoin="round"><path d="M2.5 1h2l1 2.6-1.3.9a6 6 0 0 0 3.3 3.3l.9-1.3 2.6 1v2A1.3 1.3 0 0 1 9.6 11 8.6 8.6 0 0 1 1 2.4 1.3 1.3 0 0 1 2.5 1z"/></svg>
        (+44) 1632 960 418
      </li>
      <li>
        <svg viewBox="0 0 12 12" fill="none" stroke="#e9e9e9" stroke-width="1.1"><rect x="1" y="2.5" width="10" height="7" rx="0.6"/><path d="M1 3l5 3.7L11 3"/></svg>
        Leo@fenathletics.co.uk
      </li>
      <li>
        <svg viewBox="0 0 12 12" fill="none" stroke="#e9e9e9" stroke-width="1"><circle cx="6" cy="6" r="5"/><ellipse cx="6" cy="6" rx="2.2" ry="5"/><path d="M1 6h10M1.8 3.5h8.4M1.8 8.5h8.4"/></svg>
        www.fenathletics.co.uk
      </li>
    </ul>
  </section>

  <section class="card card--back">
    <div class="wordmark">Fen Athletics</div>

    <div class="brand-row">
      <span class="brand brand--elm"><i class="brand__dot"></i>ElmStretch</span>
      <span class="brand brand--grit">Grit and Rain</span>
      <span class="brand brand--fen">Fen</span>
      <span class="brand brand--tava"><i class="brand__dot"></i>TavaPuni</span>
    </div>
  </section>
</body>
</html>
```